International Marketing Company - Web Design Project

vRelay is a well-funded start up in London developing an Online Marketing Platform for small businesses in Europe.

We require a large number of high quality business web designs for our business website builder. Our business websites are completely integrated into our Online Marketing systems and therefore it is important for designers to comply with our Design Guidelines.

This initial contest is a trial for us to open up the design process to top designers for the Builders vertical (e.g. Builders, Electricians, Plumbers, Flooring, etc.). We have implemented a base html structure and design and included them in the files.

Use your creativity to design new and fresh designs based on the included elements (e.g. testimonials, business description, etc).

We will award the stated prize money for the top three designs.

Any designers that submit designs we feel are of a high enough quality but do not make the top 3 could still be compensated and WILL be invited to participate in our next vertical competition.

Therefore, we encourage designers to submit as many designs as possible as we may award up to 25 designs.

Submissions will be reviewed daily and feedback provided where possible.

Designers who can also code will have the options to implement their designs for an additional fee.

Good luck!
Updates

There has been a mistake made in regard to the prize. Pixel Harbor should have it fixed soon.

1st place = £350
2nd place = £250
3rd Place = £150

Thanks,
Morris
25/11/2011

UPDATE:

1st place will win £350
2nd place will win £250
3rd place will win £150

Everything else is as to the specification.

Thanks
Morris

Target Market(s)

Builders, Electricians, Plumbers, Tradesman, Small construction companies

Industry/Entity Type

Business

Requirements
Must have
• Totally new designs based around the elements we want to show on each page.

We are looking for something different to the design we already have. But you can use that as a starting point.

Use the included files to see what is required for each page. Here is a brief outline:

Homepage - Testimonials, News, Business Description, Latest Projects and Call to action

About-Us - Team Summary, About the Business and a call to action

Projects Page - Project Details (Oage Title and description), Each project needs a title, content and 2 images.

Testimonials Page - The testifiers name and their comment

Contacts Page - Terrafind Map, Company address, business hours, contact form and a call to action.

Please submit final designs in Photoshop or Fireworks format.

Each page has a set of elements. These element must feature in the design of that page. See supporting documents for page details.

All elements must be included in your design. Please do not add any extra element.

Professional look and feel
Nice to have
• Design variations:
Full width designs
Boxed Designs
With AND without carousels
OR static images
Good use of stock images.

Creative use of the elements, dont be restricted/influenced by the default design we have already

Designs based on the 960 grid

```html
<!DOCTYPE html>
<html lang="en">
<head>
<meta charset="utf-8">
<title>KT Builders</title>
<link href="https://fonts.googleapis.com/css2?family=Oswald:wght@500&family=Open+Sans:wght@400;600;700&display=swap" rel="stylesheet">
<style>
:root{
  --page:#e9e9e9;
  --panel:#ffffff;
  --ink:#333333;
  --muted:#7a7a7a;
  --line:#d6d6d6;
  --accent:#f0891c;
  --dark:#2b2b2b;
  --bar:#dcdcdc;
}
*{box-sizing:border-box;margin:0;padding:0}
html,body{width:816px;height:1200px;overflow:hidden}
body{background:var(--page);font-family:"Open Sans",Arial,sans-serif;color:var(--ink);font-size:9px;line-height:1.45;position:relative}
.wrap{position:absolute;left:40px;width:736px}
.site-header{top:0;height:70px}
.brand{position:absolute;left:0;top:20px;display:flex;align-items:center;gap:8px}
.brand-mark{width:22px;height:22px;background:var(--dark)}
.brand-name{font-weight:700;font-size:24px;color:var(--ink);line-height:1}
.brand-tag{position:absolute;left:30px;top:28px;font-size:10px;color:var(--muted);white-space:nowrap}
.header-contact{position:absolute;right:0;top:10px;font-size:8px;color:var(--muted);text-align:right}
.header-contact b{color:var(--accent);font-weight:600}
.main-nav{top:74px;height:24px;background:linear-gradient(#f7f7f7,#e3e3e3);border:1px solid var(--line);display:flex;justify-content:flex-end;padding-right:24px}
.main-nav a{font-size:8px;font-weight:600;color:var(--muted);text-decoration:none;padding:0 16px;line-height:22px;text-transform:uppercase}
.main-nav a.active{color:var(--accent)}
.slider{top:104px;height:292px;background:var(--panel);border:1px solid var(--line);padding:8px;display:flex;gap:2px}
.slide-tab{width:18px;background:linear-gradient(90deg,#cfcfcf,#ececec);position:relative}
.slide-tab span{position:absolute;bottom:20px;left:4px;writing-mode:vertical-rl;transform:rotate(180deg);font-size:7px;color:var(--muted);white-space:nowrap}
.slide-photo{flex:1;background:linear-gradient(160deg,#7aaed6 0%,#c8a57a 40%,#9a6b3c 75%,#5a3e24 100%)}
.welcome{top:410px;height:120px}
.welcome h1{font-family:"Oswald",Arial,sans-serif;font-weight:500;font-size:14px;color:var(--ink);display:flex;align-items:center;gap:6px}
.welcome h1::before{content:"";width:10px;height:10px;background:var(--dark)}
.welcome p{width:590px;color:var(--muted);font-size:7.5px;margin-top:6px}
.cta{position:absolute;right:0;top:10px;width:120px;height:96px;background:linear-gradient(#3a3a3a,#1e1e1e);border-radius:6px;color:#fff;text-align:center;padding-top:20px}
.cta strong{display:block;font-family:"Oswald",Arial,sans-serif;font-weight:500;font-size:19px;line-height:1.1}
.cta span{font-size:11px;line-height:1.2;display:block}
.columns{top:560px;height:350px;display:flex;gap:24px}
.col{flex:1}
.col-head{height:22px;background:var(--bar);display:flex;align-items:center;font-family:"Oswald",Arial,sans-serif;font-size:12px;font-weight:500;margin-bottom:12px}
.col-head::before{content:"";width:22px;height:22px;background:var(--dark);margin-right:8px}
.col-head em{font-style:normal;color:var(--accent)}
.entry{color:var(--muted);font-size:7.5px;margin-bottom:14px;border-bottom:1px solid var(--line);padding-bottom:14px}
.entry .who{display:block;margin-top:10px;color:var(--ink);font-size:7px}
.more{text-align:right;font-size:7px;color:var(--muted)}
.map{height:110px;background:linear-gradient(135deg,#dfe6d6,#c9d7e4);border:1px solid var(--line)}
.address{color:var(--muted);font-size:7.5px;margin-top:10px}
.address b{color:var(--ink)}
.social{display:flex;gap:5px;margin-top:8px}
.social i{width:14px;height:14px;background:#9a9a9a;border-radius:2px}
.lower{top:950px;height:200px;display:flex;gap:24px}
.projects{flex:2}
.careers{flex:1}
.thumbs{display:flex;gap:10px}
.thumb{flex:1;text-align:center;font-size:7px;color:var(--muted)}
.thumb div{height:66px;border:3px solid var(--panel);box-shadow:0 0 0 1px var(--line);margin-bottom:6px}
.t1{background:linear-gradient(#b9b2a6,#6e6457)}
.t2{background:linear-gradient(#d9d4cc,#8d8378)}
.t3{background:linear-gradient(#c7cbd1,#767d88)}
.t4{background:linear-gradient(#d3c4aa,#8a7250)}
.career{display:flex;gap:8px;margin-bottom:10px}
.career i{width:16px;height:16px;background:var(--accent);border-radius:3px;flex:none}
.career b{display:block;color:var(--accent);font-size:8px;font-weight:600}
.career span{color:var(--muted);font-size:7px}
.site-footer{position:absolute;left:0;right:0;bottom:0;height:34px;background:var(--dark);color:#aaa;font-size:7px;display:flex;align-items:center;justify-content:space-between;padding:0 40px}
.site-footer nav a{color:#ccc;text-decoration:none;margin-left:10px;text-transform:uppercase}
</style>
</head>
<body>
<header class="wrap site-header">
  <div class="brand">
    <span class="brand-mark"></span>
    <span class="brand-name">KT Builders</span>
    <span class="brand-tag">Building homes with care</span>
  </div>
  <div class="header-contact">
    Call us now: <b>020 555 0148</b><br>
    Follow us on <b>our social pages</b>
  </div>
</header>

<nav class="wrap main-nav">
  <a class="active" href="#">Home</a>
  <a href="#">About Us</a>
  <a href="#">Testimonials</a>
  <a href="#">Portfolio</a>
  <a href="#">Contacts</a>
</nav>

<section class="wrap slider">
  <div class="slide-tab"><span>Slide 1 title</span></div>
  <div class="slide-tab"><span>Slide 2 title</span></div>
  <div class="slide-tab"><span>Slide 3 title</span></div>
  <div class="slide-photo" role="img" aria-label="Builders working on a timber roof frame under a blue sky"></div>
  <div class="slide-tab"><span>Slide 4 title</span></div>
</section>

<section class="wrap welcome">
  <h1>Welcome to KT Builders</h1>
  <p>KT Builders is an experienced building and construction company based in Crawley and the south east. We have served local homes and firms for many years, and our team takes pride in honest work, fair prices and jobs that are done on time and kept tidy from the first day to the last.</p>
  <p>Our skilled trades cover new builds, extensions, loft conversions, roofing, brickwork and full renovations. We manage every step, from plans and permits to the final finish, so you have one point of contact.</p>
  <p>Call us today for a free quote and let us show you why our clients return to us again and again.</p>
  <div class="cta"><strong>Contact Us</strong><span>for a<br>Quote Now</span></div>
</section>

<section class="wrap columns">
  <div class="col">
    <h2 class="col-head"><em>Customer</em>Say</h2>
    <div class="entry">KT Builders did a great job on our kitchen extension. The team was neat, quick and kept us updated each week.<span class="who">Mr. Sampson</span></div>
    <div class="entry">Our loft conversion was finished on budget and on time. I would happily use this firm again for any work.<span class="who">Mrs. Harlow</span></div>
    <div class="entry">Friendly staff and solid work. The new roof looks superb and the site was left clean every day.<span class="who">Mr. Delaney</span></div>
    <div class="more">Read more</div>
  </div>
  <div class="col">
    <h2 class="col-head"><em>Latest</em>News</h2>
    <div class="entry">New office opened in the town centre to serve our growing list of clients.<span class="who">12 March</span></div>
    <div class="entry">Our team has finished a large housing project on time and on budget.<span class="who">28 February</span></div>
    <div class="entry">We now offer full planning support for all home extension work.<span class="who">9 February</span></div>
    <div class="more">Read more</div>
  </div>
  <div class="col">
    <h2 class="col-head"><em>Contact</em>Information</h2>
    <div class="map" role="img" aria-label="Terrafind Map showing the office location"></div>
    <div class="address">
      <b>KT Builders</b><br>
      14 Orchard Lane, Crawley<br>
      West Sussex RH10 4QP<br>
      Phone: 020 555 0148<br>
      Email: info@ktbuilders.example
    </div>
    <div class="address"><b>Find us on</b></div>
    <div class="social"><i></i><i></i><i></i><i></i></div>
  </div>
</section>

<section class="wrap lower">
  <div class="projects">
    <h2 class="col-head"><em>Latest</em>Project</h2>
    <div class="thumbs">
      <div class="thumb"><div class="t1" role="img" aria-label="Finished house extension"></div>House extension in Crawley</div>
      <div class="thumb"><div class="t2" role="img" aria-label="Bright loft conversion interior"></div>Loft conversion in Horsham</div>
      <div class="thumb"><div class="t3" role="img" aria-label="New home build exterior"></div>Home build in Redhill</div>
      <div class="thumb"><div class="t4" role="img" aria-label="Renovated kitchen"></div>Kitchen refit in Crawley</div>
    </div>
    <div class="more" style="margin-top:10px">More project</div>
  </div>
  <div class="careers">
    <h2 class="col-head"><em>Career</em>Specializations</h2>
    <div class="career"><i></i><div><b>Home extensions</b><span>Single and double storey work.</span></div></div>
    <div class="career"><i></i><div><b>Loft conversions</b><span>More room under your own roof.</span></div></div>
    <div class="career"><i></i><div><b>Roofing work</b><span>Repairs and full new roofs.</span></div></div>
    <div class="career"><i></i><div><b>Renovations</b><span>Full refits of homes and shops.</span></div></div>
  </div>
</section>

<footer class="site-footer">
  <span>Copyright © 2012 KT Builders. All rights reserved.</span>
  <nav><a href="#">Home</a><a href="#">About Us</a><a href="#">Testimonials</a><a href="#">Portfolio</a><a href="#">Contacts</a></nav>
</footer>
</body>
</html>
```